Store Front Window Design

We have a beautiful corner store front dental practice with no window signage. Crazy I know...that's why we need your help.

The final design will be done in all vinyl unless unless you suggest a different medium (meaning we are open to some design idea like using frosted glass, etc...).

The windows provide a lot of natural light so the design needs to keep a lot of natural light coming into the office. Keep in mind vinyl is not opaque so keep the signage aesthetically pleasing and a minimalist design to allow as much natural light in as possible. The design should follow the aesthetic from our logo. or tie into at least. We want a cohesive brand aesthetic.

I submitted some general layout ideas. There is a blue banner with advertising words which we want to be used in the final version. Even though the lettering is black, in reality the letters will be a white vinyl on the outside of the window. When you submit your work, be sure to add any special instructions (aka tell me the vision for the letters is white not black, maybe gold leaf, or forested glass...stuff like that). AND YOU DO NOT HAVE TO FOLLOW MY PATTERN! YOU ARE ARTISTS AND WE ARE LOOKING FOR AN ARTISTIC EYE CATCHING PRESENTATION OF THIS INFORMATION. MAKE IT FLASHY AND ADD SOME AESTHETIC FROM THE TOOTH LOGO.

The store front is 6 windows roughly 60'' x 36'' The smaller windows below are 27'' x 36''. Around the corner there are 3 windows. they are 60'' x 27'' lower windows are 27" x 27". We would like to keep the bottom windows clear and keep the signage on the top windows, however, we are flexible.

The front 6 windows need to have this information worked into the design.

Practice name: Varden and Pellosi Dental & Orthodontics.
Phone numbers: Rosalind Varden DDS: 415.555.0187
Oskar Pellosi DDS:415.555.0243

Expertise: Dr. Varden General Dentistry & Orthodontics
Dr. Pellosi Oral Surgery & Sedation

Address: 1938 Birchwood Ave

A banner across the bottom of the top windows with some key advertisement words: "Clearmold" "Braces" "Implants" "Whiting" "Call today" "Free Consultation" "Oral Surgery" "Sedation". We like the two color idea. Its up to you to decide on the color combo. I used a Dark and light blue, but maybe a Blue and grey would nice to tire in the logo colors?

I have made some mock ideas to get the ball rolling but you do not have to stick to these designs at all, just as long as all the required information is there. Be creative with the layouts, fonts, color scheme, (just remember these are going on windows not necessarily a white background), and graphics/artistic flare (refer to logo for layout inspiration and use the logo as an actual graphic). We are running a miltimillion dollar dental practice so we want these windows to be eye catching to pull in patients and look like a million dollar design. Also all 6 windows dont need ot be used. I am really looking for creative design marketing.

The corner 3 windows need the following information: name, expertise, phone number, banner.

Dr. Varden, General Dentistry & Orthodontics, 415.555.0187
Dr. Pellosi, Oral Surgery & Sedation, 415.555.0243

There is also a front door that needs to be designed. The door is 60'' x 36'' (standard door size) We want simple white vinyl on the outside of the door. We need you to organize the information on the door, pick a easy to read font, maybe use the logo and use some of the front window signage aesthetic? Its up to you...but we we were initially thinking of just making the litters white and keep it simple but again you are the designers.

Practice name: Varden and Pellosi General Dentistry & Orthodontics

Address: 1938 Birchwood Ave

Phone numbers: Dr. Varden 415.555.0187
Dr. Pellosi 415.555.0243

Hours of operation: Mon: call for an appointment
Tues-Thurs: 9am-5pm
Sat: call for an appointment
Sun: Closed

A line saying we speak Spanish: Se Habla Espanol

*****************************************************************************************************
here are some design that we liked and some rough sketches I made to start the ball rolling. Keep in mind that there are 9 windows for the front because its a corner office, but not all of them have to have stuff on it. We want simple, streamline, classy high commanding price point aesthetic. I am hiring you for your artistic minds.

Target Market(s)

anyone who has dental needs

Industry/Entity Type

Dental

Font styles to use
Serif
Sans Serif

Colors

Designer to choose colors to be used in the design.

Requirements
Must have
• 1. The required information (see project description)
• 2. Logo
• 3. Advertisement banner running along the bottom of all 9 windows (6 in front and 3 on the side)
• NOTE: Look at pictures of the store to get a sense of the customers point of view and also as a reference to how your design will be broken up across several windows or maybe you design something special for every window. But we want the banner to run along all the windows to lead customs to the door on the side. Finally the letters will be done in white vinyl unless state otherwise, remember the window needs to let in natural light so the entire window can not be covered in vinyl.
Nice to have
• artistic flare yet simple and sleep and expensive looking aesthetic. work logo into the design.
Should not have
• The goal is to catch someone eye and give them important information about the practice.
• It should not just be words.
• It should not have to many words
• It must be readable font for cards driving by.

```html
<!DOCTYPE html>
<html lang="en">
<head>
<meta charset="utf-8">
<title>Varden and Pellosi Dental &amp; Orthodontics – Window Signage</title>
<link rel="stylesheet" href="https://fonts.googleapis.com/css2?family=Oswald:wght@400;500&family=Mulish:wght@400;600&family=Montserrat:wght@700&display=swap">
<style>
  :root {
    --brand-blue: #1a7fd1;
    --brand-blue-light: #4aa0e4;
    --brand-grey: #8f8f93;
    --grey-corner: #9b9ca0;
    --grey-corner-light: #c4c5c8;
    --text-grey: #707074;
    --paper: #ffffff;
    --backdrop: #e2e2e2;
    --ink: #111111;
  }
  * { margin: 0; padding: 0; box-sizing: border-box; }
  html, body {
    width: 1200px;
    height: 2632px;
    overflow: hidden;
    background: var(--backdrop);
  }
  .canvas {
    position: relative;
    width: 1200px;
    height: 2632px;
  }
  .window-panel {
    position: absolute;
    left: 119px;
    top: 746px;
    width: 962px;
    height: 1036px;
    box-shadow: 0 10px 22px rgba(0,0,0,0.28);
    background: var(--paper);
  }
  .window-panel svg { display: block; }
  .headline { font-family: "Oswald", sans-serif; font-weight: 500; fill: var(--brand-grey); }
  .brand-name { font-family: "Mulish", sans-serif; font-weight: 600; fill: var(--brand-grey); letter-spacing: 3px; }
  .doctor-name { font-family: "Oswald", sans-serif; font-weight: 400; fill: var(--brand-blue); }
  .phone-number { font-family: "Oswald", sans-serif; font-weight: 400; fill: var(--brand-blue); }
  .caption { font-family: "Mulish", sans-serif; font-weight: 400; fill: var(--text-grey); }
  .banner-word { font-family: "Mulish", sans-serif; font-weight: 600; fill: var(--paper); letter-spacing: 0.5px; }
  .panel-label {
    position: absolute;
    left: 0;
    width: 1200px;
    top: 1862px;
    text-align: center;
    font-family: "Montserrat", sans-serif;
    font-weight: 700;
    font-size: 34px;
    letter-spacing: 2px;
    color: var(--ink);
  }
</style>
</head>
<body>
<main class="canvas">
  <section class="window-panel">
    <svg width="962" height="1036" viewBox="0 0 962 1036" xmlns="http://www.w3.org/2000/svg">
      <defs>
        <linearGradient id="emblemFill" x1="0" y1="0" x2="0" y2="1">
          <stop offset="0" stop-color="var(--brand-blue)"/>
          <stop offset="1" stop-color="var(--brand-blue-light)"/>
        </linearGradient>
        <clipPath id="panelClip"><rect width="962" height="1036"/></clipPath>
      </defs>

      <g class="backdrop-shapes" clip-path="url(#panelClip)">
        <rect class="corner-blue" x="0" y="0" width="962" height="508" fill="var(--brand-blue)"/>
        <rect class="corner-grey" x="0" y="508" width="962" height="528" fill="var(--grey-corner)"/>
        <circle class="corner-grey-ring" cx="481" cy="508" r="572" fill="var(--grey-corner-light)"/>
        <circle class="center-circle" cx="481" cy="508" r="556" fill="var(--paper)"/>
      </g>

      <g class="brand-mark">
        <circle cx="481" cy="96" r="38" fill="var(--brand-grey)"/>
        <text class="brand-name" x="481" y="172" font-size="17" text-anchor="middle">VARDEN AND PELLOSI</text>
        <text class="brand-name" x="481" y="196" font-size="17" text-anchor="middle">DENTAL &amp; ORTHODONTICS</text>
      </g>

      <text class="headline" x="21" y="325" font-size="64" textLength="921" lengthAdjust="spacingAndGlyphs">VARDEN &amp; PELLOSI DENTAL &amp; ORTHODONTICS</text>
      <g class="headline-rule" stroke="var(--brand-blue)" stroke-width="2">
        <line x1="21" y1="336" x2="942" y2="336"/>
        <line x1="21" y1="343" x2="942" y2="343"/>
      </g>

      <g class="doctor-list">
        <text class="doctor-name" x="161" y="455" font-size="34" text-anchor="middle">DR. VARDEN</text>
        <text class="caption" x="161" y="488" font-size="18" text-anchor="middle">General Dentistry &amp; Orthodontics</text>
        <text class="doctor-name" x="161" y="598" font-size="34" text-anchor="middle">DR. PELLOSI</text>
        <text class="caption" x="161" y="631" font-size="18" text-anchor="middle">Oral Surgery &amp; Sedation</text>
      </g>

      <g class="phone-list">
        <text class="phone-number" x="481" y="455" font-size="34" text-anchor="middle">415.555.0187</text>
        <text class="caption" x="481" y="488" font-size="18" text-anchor="middle">Rosalind Varden DDS</text>
        <text class="phone-number" x="481" y="598" font-size="34" text-anchor="middle">415.555.0243</text>
        <text class="caption" x="481" y="631" font-size="18" text-anchor="middle">Oskar Pellosi DDS</text>
      </g>

      <rect class="medical-emblem" x="700" y="430" width="230" height="282" rx="14" fill="url(#emblemFill)" role="img" aria-label="Medical emblem: winged staff with two serpents"/>

      <g class="ad-banner">
        <rect x="0" y="720" width="962" height="54" fill="var(--brand-blue)"/>
        <line x1="0" y1="726" x2="962" y2="726" stroke="#ffffff" stroke-opacity="0.6" stroke-width="1" stroke-dasharray="4 4"/>
        <line x1="0" y1="768" x2="962" y2="768" stroke="#ffffff" stroke-opacity="0.6" stroke-width="1" stroke-dasharray="4 4"/>
        <text class="banner-word" x="158" y="755" font-size="22" text-anchor="middle">SEDATION</text>
        <text class="banner-word" x="481" y="755" font-size="22" text-anchor="middle">CALL TODAY</text>
        <text class="banner-word" x="802" y="755" font-size="22" text-anchor="middle">FREE CONSULTATION</text>
      </g>

      <g class="service-icons">
        <rect class="icon-sedation" x="112" y="822" width="92" height="92" rx="10" fill="var(--brand-blue)" role="img" aria-label="Icon of a patient reclining in a dental chair"/>
        <g class="icon-phone" transform="translate(436 822) scale(3.9)" fill="var(--brand-blue)">
          <path d="M6.6 10.8c1.4 2.8 3.8 5.1 6.6 6.6l2.2-2.2c.3-.3.7-.4 1-.2 1.1.4 2.3.6 3.6.6.6 0 1 .4 1 1V20c0 .6-.4 1-1 1C10.6 21 3 13.4 3 4c0-.6.4-1 1-1h3.5c.6 0 1 .4 1 1 0 1.3.2 2.5.6 3.6.1.3 0 .7-.2 1z"/>
          <path d="M14 3.2a7.2 7.2 0 0 1 6.8 6.8" fill="none" stroke="var(--brand-blue)" stroke-width="1.6" stroke-linecap="round"/>
          <path d="M14 6.6a3.8 3.8 0 0 1 3.4 3.4" fill="none" stroke="var(--brand-blue)" stroke-width="1.6" stroke-linecap="round"/>
        </g>
        <rect class="icon-consultation" x="756" y="826" width="92" height="86" rx="10" fill="var(--brand-blue)" role="img" aria-label="Icon of two people meeting across a desk"/>
      </g>
    </svg>
  </section>
  <p class="panel-label">3 WINDOWS</p>
</main>
</body>
</html>
```